Wedding Videography Wordpress Website Theme

We need a modern and high-end website look for our wedding video and film business. We film weddings all over the United Kingdom and at European destinations so need something to reflect our work. The website should be visually stunning with images and videos being the focal point as this is what our services are.

The current website is www.brunolessway.com so you will be able to see our brand.

My Photo Feed is www.instagram.com/brunolesswayfilms so a new design should link in with this idea.

We need the following pages designed by the winning designer

1 - Homepage
2 - Films Index Page
3 - Testimonials
4 - Prices
5 - Reviews
6 - Meet Bruno (About)
7 - Contact
8 - Blog Index
9 - Blog Page

All pages must be consistent so have a similar style.

Pages on menu:
Meet Bruno
Videos
Packages
Testimionials
Journal (Blog)
Contact

We require a responsive look too. Over 90% of our visitors access the website via their mobile devices.

```html
<!DOCTYPE html>
<html lang="en">
<head>
<meta charset="utf-8">
<title>Bruno Lessway Wedding Films</title>
<link rel="stylesheet" href="https://fonts.googleapis.com/css2?family=Poppins:wght@300;400;500;600&display=swap">
<style>
:root{
  --ink:#1f1f1f;
  --text:#2b2b2b;
  --muted:#555;
  --white:#fff;
  --mist:#eceef1;
  --night:#1c1c1c;
  --deep:#121212;
  --line:#cfcfcf;
}
*{box-sizing:border-box;margin:0;padding:0}
html,body{width:1200px;height:5111px;overflow:hidden}
body{position:relative;background:var(--white);font-family:'Poppins',sans-serif;color:var(--text)}
.abs{position:absolute}
.photo{position:absolute}
.btn{position:absolute;display:flex;align-items:center;justify-content:center;font-size:13px;letter-spacing:.5px;text-transform:uppercase;background:var(--ink);color:var(--white);font-weight:400}
.btn-outline{background:transparent;color:var(--ink);border:2px solid var(--ink);font-weight:600}
.site-header{position:absolute;top:0;left:0;width:1200px;height:130px;background:var(--white)}
.brand{position:absolute;text-align:center;color:var(--ink)}
.brand-name{font-weight:500;letter-spacing:4px;font-size:17px}
.brand-sub{font-size:8px;letter-spacing:4px;margin-top:2px}
.main-nav a{position:absolute;top:60px;font-size:13px;font-weight:500;color:var(--ink);text-decoration:none;letter-spacing:.5px}
.hero-panel{position:absolute;left:75px;top:268px;width:425px;height:385px;background:rgba(20,20,20,.55);color:var(--white);padding:50px 28px}
.hero-title{font-size:66px;font-weight:400;line-height:66px;letter-spacing:1px}
.hero-sub{font-size:29px;font-weight:300;line-height:40px;margin-top:22px;letter-spacing:.5px}
.hero-play{display:flex;align-items:center;gap:14px;margin-top:26px;font-size:25px;letter-spacing:1px}
.hero-play span{border-bottom:2px solid var(--white);line-height:32px}
.text-card{position:absolute;background:var(--white);border:1px solid var(--line);padding:40px 26px}
.card-title{font-size:31px;font-weight:400;line-height:42px;color:var(--ink);letter-spacing:.5px}
.card-body{font-size:14px;line-height:28px;color:var(--text);margin-top:14px}
.about{position:absolute;left:75px;top:1710px;width:510px}
.eyebrow{font-size:12px;letter-spacing:.5px;color:var(--ink)}
.about h2{font-size:22px;font-weight:500;line-height:37px;color:var(--ink);margin-top:6px}
.about p{font-size:14px;line-height:28px;margin-top:10px}
.section-title{position:absolute;width:1200px;text-align:center;font-size:48px;font-weight:400;letter-spacing:1px}
.play-ring{position:absolute;width:50px;height:50px}
.brochure-text{position:absolute;left:150px;top:2910px;font-size:26px;letter-spacing:2px;color:var(--ink);font-weight:400}
.testimonial-heading{position:absolute;left:810px;top:3130px;font-size:51px;line-height:58px;color:var(--ink);font-weight:400}
.quote-name{font-size:30px;font-weight:400;color:var(--ink);letter-spacing:1px}
.quote{font-size:15.5px;line-height:33px;margin-top:14px}
.quote-venue{font-size:12.5px;font-weight:600;margin-top:14px;letter-spacing:.3px}
.post{position:absolute;top:4008px;width:329px}
.post-thumb{height:217px}
.post h3{font-size:21px;font-weight:500;line-height:32px;color:var(--ink);margin-top:18px}
.post a{display:inline-block;margin-top:12px;font-size:13px;color:var(--ink);text-decoration:underline}
.site-footer{position:absolute;left:0;top:4435px;width:1200px;height:676px;background:var(--night);color:var(--white)}
.footer-nav a{position:absolute;top:77px;font-size:13px;font-weight:500;color:var(--white);text-decoration:none;letter-spacing:.5px}
.footer-rule{position:absolute;left:0;top:150px;width:1200px;height:1px;background:#333}
.footer-col{position:absolute;top:195px}
.footer-col h4{font-size:14px;font-weight:600;letter-spacing:.5px;margin-bottom:14px}
.footer-col li{list-style:none;font-size:14px;line-height:36px}
.contact-line{display:flex;align-items:center;gap:16px;font-size:14px;line-height:36px}
.feed-grid{position:absolute;left:434px;top:4655px;width:331px;display:grid;grid-template-columns:repeat(3,108px);grid-gap:3px}
.feed-grid div{height:108px}
.bottom-bar{position:absolute;left:0;top:610px;width:1200px;height:66px;background:var(--deep);font-size:14px;display:flex;align-items:center;padding-left:75px}
.social{position:absolute;top:22px;display:flex;gap:22px;right:75px}
.social span{width:20px;height:20px;border-radius:50%;background:var(--white)}
</style>
</head>
<body>

<header class="site-header">
  <div class="brand" style="left:60px;top:62px;width:210px">
    <div class="brand-name">BRUNO LESSWAY</div>
    <div class="brand-sub">WEDDING FILMS</div>
  </div>
  <nav class="main-nav">
    <a style="left:342px">MEET BRUNO</a>
    <a style="left:477px">VIDEOS</a>
    <a style="left:580px">PACKAGES</a>
    <a style="left:710px">TESTIMIONIALS</a>
    <a style="left:868px">JOURNAL</a>
    <a style="left:985px">CONTACT</a>
  </nav>
  <svg class="abs" style="left:1107px;top:60px" width="16" height="16" viewBox="0 0 16 16"><circle cx="6.5" cy="6.5" r="5" fill="none" stroke="#1f1f1f" stroke-width="2"/><line x1="10.3" y1="10.3" x2="15" y2="15" stroke="#1f1f1f" stroke-width="2"/></svg>
</header>

<svg class="photo" style="left:0;top:130px" width="1200" height="690" viewBox="0 0 1200 690" role="img" aria-label="Bride and groom walking through a shower of confetti">
  <defs><linearGradient id="heroG" x1="0" x2="1"><stop offset="0" stop-color="#6a4a48"/><stop offset=".5" stop-color="#3b3a4c"/><stop offset="1" stop-color="#a99d93"/></linearGradient></defs>
  <polygon points="0,0 1200,0 1200,630 600,690 0,630" fill="url(#heroG)"/>
</svg>
<div class="hero-panel">
  <div class="hero-title">BRUNO<br>LESSWAY</div>
  <div class="hero-sub">North East and Yorkshire<br>Wedding Videographer</div>
  <div class="hero-play">
    <svg width="26" height="26" viewBox="0 0 26 26"><circle cx="13" cy="13" r="11.5" fill="none" stroke="#fff" stroke-width="2"/><polygon points="10,7.5 19,13 10,18.5" fill="#fff"/></svg>
    <span>PLAY VIDEO</span>
  </div>
</div>

<div class="photo" style="left:75px;top:897px;width:691px;height:495px;background:linear-gradient(135deg,#5b5144,#8f7f6c 55%,#c7bfb2)" role="img" aria-label="Couple leaving the church under confetti"></div>
<div class="text-card" style="left:616px;top:1050px;width:510px;height:455px">
  <div class="card-title">YOUR WEDDING DAY IS THE MOST IMPORTANT DAY OF YOUR LIFE...</div>
  <p class="card-body">The celebration of your love story... and you'll want to remember it for the rest of your lives.</p>
  <p class="card-body" style="margin-top:12px">Your wedding film is the best way to keep this day alive forever ... a newlywed's gift that keeps giving ... an infinite reminder of those special moments and memories.</p>
  <div class="btn" style="left:26px;top:357px;width:172px;height:46px">READ MORE</div>
</div>

<svg class="abs" style="left:0;top:1555px" width="1200" height="645" viewBox="0 0 1200 645"><polygon points="0,0 600,65 1200,0 1200,645 0,645" fill="#eceef1"/></svg>
<div class="about">
  <div class="eyebrow">ABOUT US</div>
  <h2>Bruno lessway, a trusted and acclaimed wedding filmmaker based in the north east and yorkshire, has more than 20 years of filmmaking experience.</h2>
  <p>From beautiful barns and luxurious country hotels to sun-drenched Greek Islands and ancient Italian abbeys, he has filmed all kinds of unforgettable weddings.</p>
  <p style="margin-top:4px">If you're looking for a highly experienced wedding videographer who focuses on your story, the goosebump moments and the emotions filling the room.</p>
</div>
<div class="btn" style="left:75px;top:2083px;width:172px;height:45px">READ MORE</div>
<div class="photo" style="left:616px;top:1705px;width:510px;height:435px;background:linear-gradient(135deg,#3a3533,#1d1c1c)" role="img" aria-label="Groom overcome with emotion"></div>

<div class="abs" style="left:0;top:2200px;width:1200px;height:355px;background:linear-gradient(90deg,#1a1a1a,#2a2a2a 60%,#1a1a1a)"></div>
<div class="section-title" style="top:2245px;color:var(--white)">LATEST WEDDING</div>
<div class="photo" style="left:75px;top:2343px;width:512px;height:379px;background:linear-gradient(135deg,#a79280,#d9cfc7 60%,#ece6e1)" role="img" aria-label="Bride looking down, still from wedding film"></div>
<div class="photo" style="left:616px;top:2343px;width:510px;height:379px;background:linear-gradient(135deg,#b9bcbd,#8a8f86 55%,#5f6759)" role="img" aria-label="Aerial view of a marquee and garden"></div>
<svg class="play-ring" style="left:306px;top:2508px" viewBox="0 0 50 50"><circle cx="25" cy="25" r="22" fill="none" stroke="#fff" stroke-width="3"/><polygon points="19,14 36,25 19,36" fill="#fff"/></svg>
<svg class="play-ring" style="left:847px;top:2508px" viewBox="0 0 50 50"><circle cx="25" cy="25" r="22" fill="none" stroke="#fff" stroke-width="3"/><polygon points="19,14 36,25 19,36" fill="#fff"/></svg>

<div class="abs" style="left:0;top:2813px;width:1200px;height:232px;background:var(--mist)"></div>
<div class="brochure-text">DOWNLOAD MY WEDDING VIDEO BROCHURE</div>
<div class="btn btn-outline" style="left:830px;top:2903px;width:220px;height:54px">DOWNLOAD NOW</div>

<div class="photo" style="left:75px;top:3125px;width:691px;height:495px;background:linear-gradient(135deg,#3d3b3a,#8b8680 55%,#d6d2cc)" role="img" aria-label="Newlyweds embracing by a window"></div>
<svg class="abs" style="left:102px;top:3490px" width="96" height="96" viewBox="0 0 96 96"><circle cx="48" cy="48" r="43" fill="none" stroke="#fff" stroke-width="6"/><polygon points="37,26 72,48 37,70" fill="#fff"/></svg>
<div class="testimonial-heading">VIDEO<br>TESTIMONIAL</div>
<div class="text-card" style="left:616px;top:3278px;width:510px;height:457px;padding:48px 26px">
  <div class="quote-name">MARISA + LEON</div>
  <p class="quote">“We have a really emotional video for our wedding. It is a beauty video that is going to stay with us for the rest of our lives. Bruno was everywhere but you couldn't tell he was there. He was a really fun guy and we now consider him a friend.”</p>
  <p class="quote-venue">MARRIED AT VILLA CORVARO, UMBRIA, ITALY</p>
  <div class="btn" style="left:26px;top:357px;width:172px;height:46px">READ MORE</div>
</div>
<svg class="abs" style="left:488px;top:3665px" width="104" height="46" viewBox="0 0 104 46"><polyline points="26,6 8,23 26,40" fill="none" stroke="#1f1f1f" stroke-width="4"/><line x1="60" y1="4" x2="44" y2="42" stroke="#9a9a9a" stroke-width="2"/><polyline points="78,6 96,23 78,40" fill="none" stroke="#1f1f1f" stroke-width="4"/></svg>

<svg class="abs" style="left:0;top:3785px" width="1200" height="110" viewBox="0 0 1200 110"><polygon points="0,0 600,65 1200,0 1200,110 0,110" fill="#eceef1"/></svg>
<div class="section-title" style="top:3915px;color:var(--ink)">JOURNAL</div>
<article class="post" style="left:75px">
  <div class="post-thumb" style="background:linear-gradient(135deg,#7d8a78,#d8d2c8)" role="img" aria-label="Couple laughing under confetti outdoors"></div>
  <h3>Clara and Tom – Hollin Ford Inn Old Barn Wedding</h3>
  <a>Read More</a>
</article>
<article class="post" style="left:437px">
  <div class="post-thumb" style="background:linear-gradient(135deg,#3a2e28,#8c6f5b)" role="img" aria-label="Bride walking down the aisle in a hall"></div>
  <h3>Ashby Grange Wedding In Northumberland</h3>
  <a>Read More</a>
</article>
<article class="post" style="left:799px">
  <div class="post-thumb" style="background:linear-gradient(135deg,#6e6f6b,#e3e1dd)" role="img" aria-label="Couple with a flower girl"></div>
  <h3>The Romantic Wedding at The Grey Mare Hexley</h3>
  <a>Read More</a>
</article>

<footer class="site-footer">
  <nav class="footer-nav">
    <a style="left:75px">MEET BRUNO</a>
    <a style="left:210px">VIDEOS</a>
    <a style="left:313px">PACKAGES</a>
    <a style="left:773px">TESTIMONIALS</a>
    <a style="left:933px">JOURNAL</a>
    <a style="left:1050px">CONTACT</a>
  </nav>
  <div class="brand" style="left:495px;top:68px;width:210px;color:var(--white)">
    <div class="brand-name">BRUNO LESSWAY</div>
    <div class="brand-sub">WEDDING FILMS</div>
  </div>
  <div class="footer-rule"></div>
  <div class="footer-col" style="left:75px">
    <h4>QUICK LINKS</h4>
    <ul><li>FAQ's</li><li>Wedding Photography</li><li>Commercial</li><li>North East Wedding Venues</li><li>Free Speeches Guide</li><li>Blog</li></ul>
  </div>
  <div class="footer-col" style="left:434px"><h4>PHOTO FEED</h4></div>
  <div class="footer-col" style="left:818px">
    <h4>CONTACT US</h4>
    <div class="contact-line"><svg width="14" height="14" viewBox="0 0 14 14"><path d="M3 1l3 3-2 2c1 2 2 3 4 4l2-2 3 3-2 2C6 13 1 8 1 3z" fill="#fff"/></svg>07700 900 312</div>
    <div class="contact-line"><svg width="14" height="11" viewBox="0 0 14 11"><rect width="14" height="11" fill="#fff"/><polyline points="0,0 7,6 14,0" fill="none" stroke="#1c1c1c" stroke-width="1.5"/></svg>films@brunolessway.com</div>
    <div style="display:flex;align-items:center;gap:14px;margin-top:22px">
      <div style="text-align:center;width:142px"><div style="font-size:13px;letter-spacing:2.5px;font-weight:500">BRUNO LESSWAY</div><div style="font-size:6px;letter-spacing:3px">WEDDING FILMS</div></div>
      <div style="width:62px;height:72px;background:#e8ecf5"></div>
      <div style="width:80px;height:80px;border-radius:50%;background:#e6d94f"></div>
    </div>
  </div>
  <div class="bottom-bar">© Copyright 2022 Bruno Lessway Films Ltd All Rights Reserved
    <div class="social"><span></span><span></span><span></span><span></span><span></span></div>
  </div>
</footer>
<div class="feed-grid">
  <div style="background:#7a6a5e" role="img" aria-label="Feed photo, venue film"></div>
  <div style="background:#5a5450" role="img" aria-label="Feed photo, couple portrait"></div>
  <div style="background:#8c8279" role="img" aria-label="Feed photo, wedding moment"></div>
  <div style="background:#4a4440" role="img" aria-label="Feed photo, venue film"></div>
  <div style="background:#6f6963" role="img" aria-label="Feed photo, ceremony"></div>
  <div style="background:#3e3936" role="img" aria-label="Feed photo, reception"></div>
  <div style="background:#8a7e74" role="img" aria-label="Feed photo, venue film"></div>
  <div style="background:#b9b4a8" role="img" aria-label="Feed photo, horse and carriage"></div>
  <div style="background:#6a605a" role="img" aria-label="Feed photo, wedding details"></div>
</div>

</body>
</html>
```